Need App for Impact Related Events

My app is to help with internal events. When you enter the prompted event code the next screen shows you everyone currently at the event. It will give you the ability to Start a conversation with someone you met at that event, or signal it is your turn to send a message. The next screen is a message thread with that person. I am looking for a design that incorporates the colors and ‘feel good’ emotion of our logo. I have pieced together a pretty good interpretation of what I’m looking for in the attached mockup by slicing and dicing designs. I also attached our logo mascot.Screens (see attached mockups)

Note 1: I do not like the picture on the screen used in screen one because it makes it seem like a dating app. I attached an alternative photo that can be used or present different ideas.

Note 2: On the login/signup screen (screen 2) I need an additional first and last name for login, you can try to fit this on one login screen or present a two step signup screen where that is presented in the second screen.

READ MOCKUP GUIDELINES UNDER Must Haves

Target Market(s)

People attending internal social impact events

Industry/Entity Type

Charity

Font styles to use
Sans Serif

Colors
86cfc6

Requirements
Must have
• Follow the screen mockups attached to project
• PLEASE READ
• I have provided a relatively close design of what I’m looking for in the mockups. Some screens need to be followed more closely to my design mockup than other. I have listed a guide below how how closely you should follow my mockup design exactly. Overall I would like to see some ideas of incorporating a few accent colors so it doesn’t appear SO Blue. I also attached some app inspiration designs I found from around the web
• Screen Mockup Guideline Follow %
• Screen 1: 65% - mostly on target, would like to see ways to make it not SO Blue and possibly creative places to add some explainer text describing the app
• Screen 2: 50% - general design idea is here, but more open
• Screen 3: 35% - a lot more room for design influence
• Screen 4: 70% - mostly on target, a little room for design influence/color scheme ideas
• Screen 5-6: 25% - a lot of room for design change/ideas/influence
• Screen 7-8: 80% - already very close to what I need, maybe open to slight sizing and color scheme ideas
• Screen 9: 15% - the most open for influence, only the general functionality of the screen is communicated here
Nice to have
• Please Read Mockup Guideline above. In large part I am looking for something to use some nice accent colors so it is not overwhelmingly blue and bring the whole design into a seamless style.
Should not have

```html
<!DOCTYPE html>
<html lang="en">
<head>
<meta charset="utf-8">
<title>Messages</title>
<link href="https://fonts.googleapis.com/css2?family=Mulish:wght@400;600;700;800&display=swap" rel="stylesheet">
<style>
  :root {
    --teal: #17c6c2;
    --ink: #1e2132;
    --muted: #5d6170;
    --hint: #8a8e99;
    --rule: #e9ebee;
    --field-border: #e2e5e9;
    --paper: #ffffff;
    --avatar-a: #8c6a5c;
    --avatar-b: #6b5048;
    --avatar-c: #6a4f7a;
    --avatar-d: #5f5f63;
  }
  * { box-sizing: border-box; margin: 0; padding: 0; }
  html, body {
    width: 675px; height: 1200px; overflow: hidden;
    background: var(--paper);
    font-family: "Mulish", "Helvetica Neue", Arial, sans-serif;
    color: var(--ink);
  }
  .screen { position: relative; width: 675px; height: 1200px; }
  .abs { position: absolute; }

  .page-title { left: 30px; top: 36px; font-size: 49px; font-weight: 800; letter-spacing: 0.2px; }
  .profile-avatar { left: 579px; top: 36px; width: 64px; height: 64px; border-radius: 50%;
    background: linear-gradient(135deg, #9a9a9d, var(--avatar-d)); }

  .search-field { left: 56px; top: 141px; width: 563px; height: 75px;
    border: 2px solid var(--field-border); border-radius: 6px; }
  .search-field span { position: absolute; left: 26px; top: 22px; font-size: 26px; color: var(--hint); }
  .search-field svg { position: absolute; right: 24px; top: 22px; }

  .section-label { left: 30px; font-size: 36px; font-weight: 700; }
  .divider { left: 0; width: 675px; height: 2px; background: var(--rule); }

  .avatar { width: 64px; height: 64px; border-radius: 50%; left: 39px; }
  .contact-name { left: 133px; font-size: 30px; font-weight: 700; }
  .preview { left: 133px; font-size: 25px; color: var(--muted); white-space: nowrap; }
  .preview.pending { color: var(--teal); font-weight: 800; }
  .time { right: 28px; font-size: 21px; color: var(--muted); }

  .action-bar { left: 0; top: 920px; width: 675px; height: 280px; background: var(--paper); }
  .action-circle { width: 84px; height: 84px; border-radius: 50%; background: var(--teal);
    display: flex; align-items: center; justify-content: center; }
  .action-label { font-size: 26px; font-weight: 600; letter-spacing: 2.5px; text-align: center; width: 300px; }

  .nav-icon { top: 1130px; }
  .nav-dot { left: 194px; top: 1097px; width: 18px; height: 18px; border-radius: 50%; background: var(--teal); }
  .fab { left: 287px; top: 1084px; width: 104px; height: 104px; border-radius: 50%; background: var(--teal);
    display: flex; align-items: center; justify-content: center; }
</style>
</head>
<body>
<main class="screen">
  <h1 class="abs page-title">Messages</h1>
  <div class="abs profile-avatar" role="img" aria-label="Profile photo of the signed-in user"></div>

  <div class="abs search-field">
    <span>Search for messages</span>
    <svg width="34" height="34" viewBox="0 0 34 34" fill="none" stroke="var(--teal)" stroke-width="3.5" stroke-linecap="round">
      <circle cx="14" cy="14" r="11"/><line x1="22" y1="22" x2="30" y2="30"/>
    </svg>
  </div>

  <h2 class="abs section-label" style="top:262px">Unread</h2>
  <div class="abs divider" style="top:331px"></div>

  <div class="abs avatar" style="top:380px;background:linear-gradient(135deg,#b08a78,var(--avatar-a))" role="img" aria-label="Contact photo of Nora Bellamy"></div>
  <div class="abs contact-name" style="top:376px">Nora Bellamy</div>
  <div class="abs preview pending" style="top:422px">Waiting for your response.</div>
  <div class="abs divider" style="top:487px"></div>

  <h2 class="abs section-label" style="top:521px">Chats</h2>
  <div class="abs divider" style="top:584px"></div>

  <div class="abs avatar" style="top:639px;background:linear-gradient(135deg,#9a7666,var(--avatar-b))" role="img" aria-label="Contact photo of Owen Hartley"></div>
  <div class="abs contact-name" style="top:632px">Owen Hartley</div>
  <div class="abs preview" style="top:682px">You: Nice to meet you!</div>
  <div class="abs time" style="top:634px">12:49</div>
  <div class="abs divider" style="top:743px"></div>

  <div class="abs avatar" style="top:795px;background:linear-gradient(135deg,#8e6ea0,var(--avatar-c))" role="img" aria-label="Contact photo of Clara Fenwick"></div>
  <div class="abs contact-name" style="top:792px">Clara Fenwick</div>
  <div class="abs preview" style="top:841px">Great, we’ll discuss this idea further.</div>
  <div class="abs time" style="top:790px">03:51</div>
  <div class="abs divider" style="top:905px"></div>

  <section class="abs action-bar">
    <div class="abs action-circle" style="left:164px;top:19px">
      <svg width="36" height="36" viewBox="0 0 36 36" stroke="#fff" stroke-width="3.5" stroke-linecap="round"><line x1="18" y1="5" x2="18" y2="31"/><line x1="5" y1="18" x2="31" y2="18"/></svg>
    </div>
    <div class="abs action-label" style="left:56px;top:124px">CREATE EVENT</div>

    <div class="abs action-circle" style="left:442px;top:19px">
      <svg width="36" height="36" viewBox="0 0 36 36" fill="none" stroke="#fff" stroke-width="3.5" stroke-linecap="round">
        <path d="M4 12V4h8M24 4h8v8M32 24v8h-8M12 32H4v-8"/><line x1="10" y1="18" x2="26" y2="18"/>
      </svg>
    </div>
    <div class="abs action-label" style="left:334px;top:124px">ENTER CODE</div>
  </section>

  <svg class="abs nav-icon" style="left:46px" width="46" height="46" viewBox="0 0 46 46" fill="none" stroke="var(--teal)" stroke-width="3.5" stroke-linecap="round">
    <rect x="4" y="8" width="38" height="34" rx="4"/><line x1="4" y1="18" x2="42" y2="18"/><line x1="14" y1="3" x2="14" y2="11"/><line x1="32" y1="3" x2="32" y2="11"/>
  </svg>

  <div class="abs nav-dot"></div>
  <svg class="abs nav-icon" style="left:181px" width="46" height="46" viewBox="0 0 46 46" fill="none" stroke="var(--teal)" stroke-width="3.5" stroke-linejoin="round">
    <path d="M23 4a19 19 0 1 0 0 38h19V23A19 19 0 0 0 23 4z"/>
  </svg>

  <div class="abs fab">
    <svg width="40" height="40" viewBox="0 0 40 40" stroke="#fff" stroke-width="4" stroke-linecap="round"><line x1="8" y1="8" x2="32" y2="32"/><line x1="32" y1="8" x2="8" y2="32"/></svg>
  </div>

  <svg class="abs nav-icon" style="left:450px" width="46" height="46" viewBox="0 0 46 46" fill="none" stroke="var(--teal)" stroke-width="3.5" stroke-linejoin="round" stroke-linecap="round">
    <path d="M11 33V20a12 12 0 0 1 24 0v13l4 3H7z"/><path d="M19 40a4 4 0 0 0 8 0"/>
  </svg>

  <svg class="abs nav-icon" style="left:584px" width="48" height="46" viewBox="0 0 48 46" fill="none" stroke="var(--teal)" stroke-width="3.5" stroke-linecap="round">
    <line x1="3" y1="14" x2="45" y2="14"/><line x1="3" y1="32" x2="45" y2="32"/>
    <circle cx="31" cy="14" r="5" fill="#fff"/><circle cx="17" cy="32" r="5" fill="#fff"/>
  </svg>
</main>
</body>
</html>
```